Web design for small empirical brand consulting company that will sell a web-based brand tool

We need a totally new and very appealing website:
Purpose: We want to attract lots of potential customers with this website... especially, we want to sell our web-based tool valuquant®... we want to be perceived as innovative, trendy, but solid and reliable… we want customers go to the website, login at „valuquant®“ (see structure), and perceive how it works.. and the contacting us or in the near future being able to buy a login and work with the tool… so we want to a) inform (on the website or send the url to customers) and b) to „force“ potential customers getting in contact with us…
Structure (e.g.): Must Home, valuquant®, About us, Contact (incl. legal notice); we are open for more, Nice to have e.g. references/clients, press... for example, we publish a nice book in a couple of months and might want to show it somewhere on the website as well...)
Layout: We would like to have more/mainly figures - may be animated or something like that – in specific those on slides 7 and 8 as well as 6 and 9 (which would be for our web-based tool valuquant®...)... excellent, but simple and with few text…
Fonts: Eurostile; CMYK 100/23/100/19, CMYK 0/0/0/70
Logo: Would you please use the lorentavo-logo used in this file?
Social Media: we think that it might make sense to be connected to chatterbay, quipline and so on as well…
Phantasy: May be it is possible to have something between a classic marketing research and an e-commerce website... just a thought... because it is mainly about the new tool that will be assessable through a login... but customers might want to contact us or vice versa in order to check how the tool will work (btw: you do not have further info about valuquant® here... I know)… I dream of having a site where people go to and by components of our tool like at brimbo… click and buy and go for it…
It is possible to program it in php or java? Thanks.
Pages I personally like: Don’t know if that helps, but I personally like those websites just they seem so simple: http:// www.pellivarn.com/, http://www.craftelune.net/... but I am veeery open
Pages I do not like anymore: my own www.lorentavo.ch

```html
<!DOCTYPE html>
<html lang="en">
<head>
<meta charset="utf-8">
<title>lorentavo – brand research and brand consulting</title>
<link href="https://fonts.googleapis.com/css2?family=Signika:wght@300;400;600&display=swap" rel="stylesheet">
<style>
:root{
  --green:#0b6b32;
  --ink:#4d4d4d;
  --muted:#6f6f6f;
  --light:#f2f2f2;
  --white:#ffffff;
  --footer:#3a3a3a;
  --footer-bottom:#2b2b2b;
  --footer-text:#bdbdbd;
}
*{margin:0;padding:0;box-sizing:border-box}
html,body{width:1200px;height:2230px;overflow:hidden}
body{font-family:"Signika",Arial,sans-serif;color:var(--ink);background:var(--white);position:relative}
.abs{position:absolute}

/* header */
.site-header{position:absolute;left:0;top:0;width:1200px;height:90px;background:var(--white)}
.brand{position:absolute;left:132px;top:18px}
.brand-name{font-size:34px;font-weight:300;color:var(--ink);letter-spacing:-.5px;line-height:1}
.lang{position:absolute;left:20px;top:38px;font-size:14px;color:var(--muted);white-space:nowrap;font-weight:300}
.lang span{color:var(--ink);font-weight:400}
.main-nav{position:absolute;left:566px;top:0;height:90px;display:flex}
.main-nav a{display:block;height:90px;line-height:104px;padding:0 11px;font-size:14px;color:var(--muted);text-decoration:none;font-weight:300}
.main-nav a.active{color:var(--green);background:#fafafa;border-top:3px solid var(--green);line-height:98px;padding:0 20px}
.search-btn{position:absolute;left:1030px;top:33px;width:38px;height:33px;background:#e6e6e6}

/* hero */
.hero{position:absolute;left:0;top:90px;width:1200px;height:565px}
.hero-photo{position:absolute;inset:0;background:linear-gradient(100deg,#d9dcdc 0%,#eef0ef 35%,#e5e3df 60%,#c9bfae 100%)}
.hero-title{position:absolute;right:197px;background:rgba(255,255,255,.85);color:var(--green);font-size:35px;font-weight:300;padding:2px 16px;line-height:1.2}
.hero-sub{position:absolute;left:588px;top:272px;width:413px;background:rgba(255,255,255,.7);font-size:16px;font-weight:300;color:var(--ink);text-align:right;padding:10px 16px;line-height:1.5}
.hero-arrow{position:absolute;top:255px;width:54px;height:54px;border:2px solid rgba(255,255,255,.8);border-radius:50%;background:rgba(0,0,0,.08)}
.hero-arrow svg{position:absolute;left:18px;top:18px}

/* sections */
.section-title{position:absolute;left:0;width:1200px;text-align:center;font-size:32px;font-weight:400;color:var(--ink)}
.section-title .accent{color:var(--green)}
.body-text{font-size:13.5px;font-weight:300;line-height:1.95;color:var(--muted)}
.btn{position:absolute;background:var(--green);color:var(--white);font-size:15px;text-align:center;line-height:43px;height:43px}

.tool{position:absolute;left:0;top:655px;width:1200px;height:413px}
.tool-sub{position:absolute;left:0;top:118px;width:1200px;text-align:center;font-size:17px;font-weight:300}
.tool-shot{position:absolute;left:138px;top:170px;width:383px;height:195px;border:1px solid #cfcfcf;background:var(--white);padding:14px}
.about{position:absolute;left:0;top:1068px;width:1200px;height:302px;background:var(--light)}
.press{position:absolute;left:0;top:1370px;width:1200px;height:335px}
.press-photo{position:absolute;top:130px;width:211px;height:133px}
.press-title{position:absolute;top:138px;font-size:17px;font-weight:400;color:var(--green)}
.press-text{position:absolute;top:170px;width:218px;font-size:13px;font-weight:300;line-height:1.7;color:var(--muted)}
.press-more{position:absolute;top:250px;font-size:13px;font-weight:300;color:var(--green)}
.clients{position:absolute;left:0;top:1705px;width:1200px;height:216px;background:var(--light)}
.client{position:absolute;top:100px;width:126px;height:72px;background:var(--white);border:1px solid #e3e3e3;display:flex;align-items:center;justify-content:center;gap:6px;font-size:15px;font-weight:600;color:var(--ink)}
.client i{display:block;width:10px;height:10px;background:var(--ink)}

/* footer */
.site-footer{position:absolute;left:0;top:1921px;width:1200px;height:256px;background:var(--footer)}
.footer-head{position:absolute;top:27px;font-size:18px;color:var(--white);font-weight:300}
.footer-list{position:absolute;list-style:none;font-size:13.5px;font-weight:300;color:var(--footer-text)}
.footer-list li{height:31px;padding-left:20px;position:relative}
.footer-list li::before{content:"";position:absolute;left:0;top:7px;width:6px;height:6px;border:1px solid var(--footer-text);border-radius:50%}
.social{position:absolute;left:636px;list-style:none;top:66px}
.social li{height:38px;display:flex;align-items:center;gap:14px;font-size:13.5px;color:var(--footer-text);font-weight:300}
.social i{display:block;width:24px;height:24px;background:#5a5a5a}
.contact{position:absolute;left:837px;top:66px;width:240px;font-size:13.5px;font-weight:300;color:var(--footer-text);line-height:1.6}
.contact strong{color:var(--white);font-weight:400}
.copyright{position:absolute;left:0;top:2177px;width:1200px;height:53px;background:var(--footer-bottom);color:var(--footer-text);font-size:13px;text-align:center;line-height:53px;font-weight:300}
</style>
</head>
<body>

<header class="site-header">
  <div class="brand">
    <div class="brand-name">lorentavo</div>
    <div class="lang">English <span>German</span></div>
  </div>
  <nav class="main-nav">
    <a class="active">Home</a><a>lorentavo</a><a>Services</a><a>Work</a><a>Credentials</a><a>Contact</a>
  </nav>
  <div class="search-btn">
    <svg width="38" height="33" viewBox="0 0 38 33"><circle cx="18" cy="15" r="4.5" fill="none" stroke="#8a8a8a" stroke-width="1.8"/><line x1="21" y1="18" x2="24" y2="21" stroke="#8a8a8a" stroke-width="2"/></svg>
  </div>
</header>

<section class="hero">
  <div class="hero-photo" role="img" aria-label="Photo of a smiling consultant holding a tablet in a bright open-plan office with colleagues at desks"></div>
  <div class="hero-title" style="top:138px">Brand research and</div>
  <div class="hero-title" style="top:199px">brand consulting</div>
  <div class="hero-sub">You get an exact brand profile, tailored advertising and thus more successful.</div>
  <div class="hero-arrow" style="left:99px"><svg width="14" height="14" viewBox="0 0 14 14"><path d="M9 2 L4 7 L9 12" fill="none" stroke="#fff" stroke-width="2"/></svg></div>
  <div class="hero-arrow" style="left:1048px"><svg width="14" height="14" viewBox="0 0 14 14"><path d="M5 2 L10 7 L5 12" fill="none" stroke="#fff" stroke-width="2"/></svg></div>
</section>

<section class="tool">
  <h2 class="section-title" style="top:72px;color:var(--green)">valuquant®</h2>
  <p class="tool-sub">You get a precise, fast and reliable monitoring using innovative web methods.</p>
  <div class="tool-shot">
    <svg width="353" height="165" viewBox="0 0 353 165">
      <line x1="0" y1="20" x2="353" y2="20" stroke="#ddd"/>
      <rect x="0" y="50" width="56" height="28" rx="3" fill="#0b6b32"/>
      <rect x="0" y="83" width="56" height="28" rx="3" fill="#0b6b32"/>
      <rect x="0" y="116" width="56" height="28" rx="3" fill="#0b6b32"/>
      <rect x="0" y="149" width="56" height="16" rx="3" fill="#0b6b32"/>
      <rect x="72" y="42" width="42" height="11" rx="5" fill="#e4e4e4" stroke="#0b6b32"/>
      <rect x="124" y="42" width="42" height="11" rx="5" fill="#d4d4d4"/>
      <rect x="176" y="42" width="42" height="11" rx="5" fill="#d4d4d4"/>
      <rect x="228" y="42" width="42" height="11" rx="5" fill="#d4d4d4"/>
      <rect x="280" y="42" width="42" height="11" rx="5" fill="#d4d4d4"/>
      <line x1="72" y1="135" x2="200" y2="135" stroke="#bbb"/>
      <rect x="88" y="120" width="12" height="15" fill="#ccc"/>
      <rect x="108" y="120" width="12" height="15" fill="#ccc"/>
      <rect x="128" y="118" width="12" height="17" fill="#ccc"/>
      <rect x="148" y="116" width="12" height="19" fill="#0b6b32"/>
      <rect x="168" y="100" width="12" height="35" fill="#0b6b32"/>
      <line x1="218" y1="135" x2="345" y2="135" stroke="#bbb"/>
      <rect x="232" y="120" width="12" height="15" fill="#ccc"/>
      <rect x="252" y="120" width="12" height="15" fill="#ccc"/>
      <rect x="272" y="118" width="12" height="17" fill="#ccc"/>
      <rect x="292" y="114" width="12" height="21" fill="#0b6b32"/>
      <rect x="312" y="112" width="12" height="23" fill="#0b6b32"/>
    </svg>
  </div>
  <p class="body-text abs" style="left:558px;top:172px;width:495px">Lorem ipsum dolor sit amet, consectetur adipisicing elit, sed do eiusmod tempor incididunt ut labore et dolore magna aliqua. Ut enim ad minim veniam, quis nostrud exercitation ullamco laboris nisi ut aliquip ex ea commodo consequat. Lorem ipsum dolor sit amet, consectetur adipisicing elit, sed do eiusmod.</p>
  <div class="btn" style="left:558px;top:304px;width:128px">Learn More</div>
</section>

<section class="about">
  <h2 class="section-title" style="top:36px">About <span class="accent">Us</span></h2>
  <p class="body-text abs" style="left:140px;top:102px;width:920px;text-align:center">Lorem ipsum dolor sit amet, consectetur adipisicing elit, sed do eiusmod tempor incididunt ut labore et dolore magna aliqua. Ut enim ad minim veniam, quis nostrud exercitation ullamco laboris nisi ut aliquip ex ea commodo consequat. Lorem ipsum dolor sit amet, consectetur adipisicing elit, sed do eiusmod tempor incididunt ut labore et dolore magna aliqua.</p>
  <div class="btn" style="left:543px;top:209px;width:113px;height:42px;line-height:42px">Learn More</div>
</section>

<section class="press">
  <h2 class="section-title" style="top:62px"><span class="accent">Press</span> Release</h2>
  <div class="press-photo" style="left:130px;background:linear-gradient(90deg,#e9ecef,#d8d2c8,#eef0f2)" role="img" aria-label="Photo of a businesswoman with arms crossed in an office"></div>
  <h3 class="press-title" style="left:366px">Adipisicing elit</h3>
  <p class="press-text" style="left:366px">Lorem ipsum dolor sit amet, consect etur adipisicing elit, sed do eiusmod tempor aliqua.</p>
  <span class="press-more" style="left:366px">More &gt;&gt;</span>
  <div class="press-photo" style="left:612px;background:linear-gradient(90deg,#6d7d6a,#c8d0cf,#2f3a4a)" role="img" aria-label="Photo of business people shaking hands at a meeting"></div>
  <h3 class="press-title" style="left:852px">Ullamco laboris nis</h3>
  <p class="press-text" style="left:852px">Lorem ipsum dolor sit amet, consect etur adipisicing elit, sed do eiusmod tempor aliqua.</p>
  <span class="press-more" style="left:852px">More &gt;&gt;</span>
</section>

<section class="clients">
  <h2 class="section-title" style="top:50px;font-size:28px;font-weight:300">Our <span class="accent">Clients</span></h2>
  <div class="client" style="left:144px"><i></i>Ambrista</div>
  <div class="client" style="left:302px">Norvelle</div>
  <div class="client" style="left:460px"><i style="border-radius:50%"></i>Ambrista</div>
  <div class="client" style="left:618px">Ambrista</div>
  <div class="client" style="left:776px"><i style="border-radius:50%"></i>Quellmark</div>
  <div class="client" style="left:934px">Ambrista</div>
</section>

<footer class="site-footer">
  <h4 class="footer-head" style="left:130px">QUICKLINKS</h4>
  <ul class="footer-list" style="left:130px;top:68px">
    <li>Ut enim ad minim veniam</li><li>Quis nostrud exercitation</li><li>Ullamco laboris nisi aliquip</li><li>Commodo consequat</li><li>Duis aute irure dolor</li>
  </ul>
  <ul class="footer-list" style="left:370px;top:32px">
    <li>Ut enim ad minim</li><li>Quis nostrud exercit</li><li>Ullamco laboris aliquip</li><li>Commodo conseq</li><li>Duis aute irure dolor</li><li>Lorem ipsum dolor amet</li>
  </ul>
  <h4 class="footer-head" style="left:636px">FOLLOW US</h4>
  <ul class="social">
    <li><i></i>quipline</li><li><i></i>chatterbay</li><li><i></i>Tubelore</li><li><i></i>Postwick</li>
  </ul>
  <h4 class="footer-head" style="left:837px">CONTACT US</h4>
  <div class="contact">
    <p><strong><svg width="10" height="13" viewBox="0 0 10 13" style="margin-right:8px"><path d="M5 0 A5 5 0 0 1 10 5 C10 8 5 13 5 13 C5 13 0 8 0 5 A5 5 0 0 1 5 0Z" fill="#fff"/><circle cx="5" cy="5" r="1.8" fill="#3a3a3a"/></svg>Main Office Morocco</strong></p>
    <p style="margin-top:10px">38 Building Name, Street Name, City ZipCode</p>
    <p style="margin-top:10px"><strong>phone numbers:</strong> +(66)-02-555-0148-3</p>
    <p><strong>email:</strong> info@lorentavo.org</p>
  </div>
</footer>
<div class="copyright">Copyright&nbsp; 2014&nbsp; Your Site&nbsp;&nbsp;&nbsp; All rights reserved.</div>

</body>
</html>
```